bRu Design Group - architect web site

need a web site to permit potential clients to view our portfolio of work.

Will need lots of photos included.

Industry/Entity Type

Architect

Coding

Coded - Design and coding required

Number of Pages Required

5+ page

Font styles to use
Sans Serif

Requirements
Must have
• photos should be organized by project - perhaps a summary of photos and then click to enlarge? should be simple to operate. should be able to separate interior design from architecture.
• needs to be easy to add more photos in the future.

```html
<!DOCTYPE html>
<html lang="en">
<head>
<meta charset="utf-8">
<title>bRu Design Group</title>
<link href="https://fonts.googleapis.com/css2?family=Oswald:wght@300;400&family=Roboto:wght@400;500&display=swap" rel="stylesheet">
<style>
:root{
  --header:#8b8a90;
  --accent:#a2c3cb;
  --page:#f2f2f2;
  --ink:#2e2e2e;
  --card:#ffffff;
  --caption:#4a4a4a;
  --footer:#2b2b2b;
  --footer-text:#e6e6e6;
}
*{margin:0;padding:0;box-sizing:border-box}
html,body{width:678px;height:1200px;overflow:hidden;background:var(--page);font-family:'Roboto',sans-serif}
.site{position:relative;width:678px;height:1200px}
.site-header{position:absolute;left:0;top:0;width:678px;height:73px;background:var(--header);border-bottom:3px solid var(--accent)}
.brand{position:absolute;left:66px;top:12px;color:#fff;font-family:'Oswald',sans-serif;line-height:1}
.brand-name{font-size:34px;font-weight:400;letter-spacing:-1px}
.brand-sub{display:block;font-size:7px;letter-spacing:2px;margin-top:3px;color:#fff}
.main-nav{position:absolute;top:30px;left:0;width:100%;font-size:8.5px;color:#fff;text-transform:uppercase}
.main-nav a{position:absolute;color:inherit;text-decoration:none}
.main-nav a.is-active{color:var(--accent)}
.hero{position:absolute;left:0;top:73px;width:678px;height:338px;background:linear-gradient(180deg,#3f79c2 0%,#8db3dd 30%,#d9d3a6 48%,#6b6a52 62%,#4d7a2d 78%,#2f5a1c 100%)}
.hero-shadow{position:absolute;left:60px;top:411px;width:558px;height:14px;background:radial-gradient(ellipse at top,rgba(0,0,0,.18),rgba(0,0,0,0) 70%)}
.hero-caption{position:absolute;left:58px;top:158px;color:#fff;font-family:'Oswald',sans-serif;text-transform:uppercase;text-shadow:0 1px 3px rgba(0,0,0,.4)}
.hero-title{font-size:27px;font-weight:400;line-height:1.1}
.hero-text{font-size:15.5px;font-weight:300;line-height:23px;margin-top:8px}
.hero-controls{position:absolute;left:59px;top:327px;display:flex;gap:1px}
.hero-controls span{width:22px;height:28px;background:rgba(0,0,0,.75);display:flex;align-items:center;justify-content:center}
.section-title{position:absolute;left:50px;top:438px;font-family:'Oswald',sans-serif;font-weight:400;font-size:15px;color:var(--ink);text-transform:uppercase}
.section-title em{font-style:normal;color:var(--accent)}
.project-grid{position:absolute;left:50px;top:468px;display:grid;grid-template-columns:repeat(3,186px);column-gap:10px;row-gap:13px}
.project-card{width:186px;background:var(--card);box-shadow:0 1px 3px rgba(0,0,0,.18)}
.project-photo{height:117px}
.project-name{height:28px;display:flex;align-items:center;justify-content:center;font-size:7px;color:var(--caption);text-transform:uppercase;letter-spacing:.2px}
.site-footer{position:absolute;left:0;top:1111px;width:678px;height:89px;background:var(--footer);border-top:4px solid var(--accent)}
.footer-brand{position:absolute;left:52px;top:22px;color:#fff;font-family:'Oswald',sans-serif;line-height:1}
.footer-brand .brand-name{font-size:24px}
.footer-brand .brand-sub{font-size:5px;letter-spacing:1.5px;margin-top:2px;color:var(--accent)}
.footer-links{position:absolute;left:121px;top:31px;font-size:7px;color:var(--footer-text)}
.copyright{position:absolute;left:121px;top:48px;font-size:8px;color:var(--footer-text)}
.social{position:absolute;left:535px;top:37px;display:flex;gap:5px}
.social span{width:19px;height:19px;display:block}
</style>
</head>
<body>
<div class="site">
  <header class="site-header">
    <div class="brand"><span class="brand-name">bRu</span><span class="brand-sub">DESIGN GROUP</span></div>
    <nav class="main-nav">
      <a class="is-active" style="left:286px">Home</a>
      <a style="left:329px">About Us</a>
      <a style="left:388px">Porfolio</a>
      <a style="left:447px">Features</a>
      <a style="left:507px">News</a>
      <a style="left:549px">Blog</a>
      <a style="left:590px">Contact</a>
    </nav>
  </header>

  <section class="hero" role="img" aria-label="Yellow two-storey villa with a turret, lawn and palm fronds under a blue sky">
    <div class="hero-caption">
      <h1 class="hero-title">Architect to Exhibit</h1>
      <p class="hero-text">Lorem Ipsum is simply dummy text of the<br>printing and typesetting industry</p>
    </div>
    <div class="hero-controls">
      <span><svg width="8" height="14" viewBox="0 0 8 14"><path d="M7 1L1 7l6 6" fill="none" stroke="#fff" stroke-width="1.2"/></svg></span>
      <span><svg width="8" height="14" viewBox="0 0 8 14"><path d="M1 1l6 6-6 6" fill="none" stroke="#fff" stroke-width="1.2"/></svg></span>
    </div>
  </section>
  <div class="hero-shadow"></div>

  <h2 class="section-title">Recent <em>Projects</em></h2>
  <main class="project-grid">
    <article class="project-card"><div class="project-photo" role="img" aria-label="Long dining room with chandelier and ocean view" style="background:linear-gradient(#e8e6e2,#b9ad98)"></div><p class="project-name">Ipsum is simply dummy text</p></article>
    <article class="project-card"><div class="project-photo" role="img" aria-label="Bathroom with freestanding tub and timber beams" style="background:linear-gradient(#c98a45,#e4d8c6)"></div><p class="project-name">Ipsum is simply dummy text</p></article>
    <article class="project-card"><div class="project-photo" role="img" aria-label="Timber staircase in a white hallway" style="background:linear-gradient(#eeeeec,#b3703f 70%,#4b4540)"></div><p class="project-name">Ipsum is simply dummy text</p></article>
    <article class="project-card"><div class="project-photo" role="img" aria-label="Living room with wide windows over the sea" style="background:linear-gradient(#eef0f1,#8ea7b1 50%,#ddd7cd)"></div><p class="project-name">Ipsum is simply dummy text</p></article>
    <article class="project-card"><div class="project-photo" role="img" aria-label="Open kitchen and lounge with dark tiled floor" style="background:linear-gradient(#ece8e2,#8d7460 55%,#4a4642)"></div><p class="project-name">Ipsum is simply dummy text</p></article>
    <article class="project-card"><div class="project-photo" role="img" aria-label="Dining hall with long table and chandelier" style="background:linear-gradient(#e9e8e6,#a69682 65%,#5e5750)"></div><p class="project-name">Ipsum is simply dummy text</p></article>
    <article class="project-card"><div class="project-photo" role="img" aria-label="White entry hall with dark floor tiles" style="background:linear-gradient(#f4f2ee,#d2c9bc 60%,#4e4a46)"></div><p class="project-name">Ipsum is simply dummy text</p></article>
    <article class="project-card"><div class="project-photo" role="img" aria-label="Dining room opening onto a garden terrace" style="background:linear-gradient(#ecece9,#8fa27d 45%,#c9b9a2)"></div><p class="project-name">Ipsum is simply dummy text</p></article>
    <article class="project-card"><div class="project-photo" role="img" aria-label="Spiral staircase seen from below with chandelier" style="background:radial-gradient(circle at 50% 40%,#f4f4f4,#b9c8d6 60%,#4d4a48)"></div><p class="project-name">Ipsum is simply dummy text</p></article>
    <article class="project-card"><div class="project-photo" role="img" aria-label="Kitchen with wine fridge and built-in oven" style="background:linear-gradient(90deg,#8a6a4c,#e6e4e0 60%,#c9c6c1)"></div><p class="project-name">Ipsum is simply dummy text</p></article>
    <article class="project-card"><div class="project-photo" role="img" aria-label="Steel pergola beams against a blue sky" style="background:linear-gradient(#1a55a6,#4c86c8)"></div><p class="project-name">Ipsum is simply dummy text</p></article>
    <article class="project-card"><div class="project-photo" role="img" aria-label="White bathroom with stone floor and bath" style="background:linear-gradient(#f3f4f4,#a9a59d)"></div><p class="project-name">Ipsum is simply dummy text</p></article>
  </main>

  <footer class="site-footer">
    <div class="footer-brand"><span class="brand-name">bRu</span><span class="brand-sub">DESIGN GROUP</span></div>
    <p class="footer-links">About &nbsp;|&nbsp; Disclaimer &nbsp;|&nbsp; Contact &nbsp;|&nbsp; Sitemap</p>
    <p class="copyright">Copyright © 2015 &nbsp;All Rights</p>
    <div class="social" aria-label="Social links">
      <span style="background:#2aa3d9"></span>
      <span style="background:#c4302b"></span>
      <span style="background:#3b5a98"></span>
      <span style="background:#1e7fb6"></span>
    </div>
  </footer>
</div>
</body>
</html>
```